Professional and creative business card design for recruiting service providers

Our company supports German medium-sized companies in filling vacancies promptly. For this we use social media marketing and bring our customers into the visibility.

We want a professional but also creative design for our business cards.

Please look at lindqvar-staff.de to get an impression of our CI.

Target Market(s)

Small and medium-sized companies in Germany from the industry

Industry/Entity Type

Industrie, Handwerk

Contact Information for Business Card

Name, Position, Telefonnummer, Email, Website

Colors
EE7325
F08F49
F5BC92
FAE3D3
FDF4ED

Requirements
Must have
• A picture of the employee and in the style of www.lindqvar-staff.de

```html
<!DOCTYPE html>
<html lang="de">
<head>
<meta charset="utf-8">
<title>Lindqvar Staff – Visitenkarte</title>
<link rel="stylesheet" href="https://fonts.googleapis.com/css2?family=Jost:wght@500;600;700&family=Arimo:wght@400&display=swap">
<style>
  :root {
    --stage: #262626;
    --paper: #ffffff;
    --paper-shade: #ececec;
    --brand: #ef5f2f;
    --brand-light: #f08f49;
    --brand-deep: #dc5630;
    --ink: #111111;
    --photo-top: #d9d6d3;
    --photo-bottom: #2b2d36;
  }
  * { margin: 0; padding: 0; box-sizing: border-box; }
  html, body { width: 1065px; height: 1200px; overflow: hidden; }
  body { background: var(--stage); position: relative; font-family: "Arimo", Arial, sans-serif; }

  .card { position: absolute; width: 582px; height: 362px; box-shadow: 3px 4px 4px rgba(0,0,0,.55); overflow: hidden; }

  /* Front */
  .card--front {
    left: 292px; top: 218px;
    background: linear-gradient(160deg, var(--paper) 55%, var(--paper-shade) 100%);
    border-radius: 0 181px 181px 0;
  }
  .brand { position: absolute; display: flex; align-items: center; }
  .brand__square { background: var(--brand); }
  .brand__name { font-family: "Jost", sans-serif; font-weight: 700; letter-spacing: 1.5px; line-height: 1.05; text-transform: uppercase; }
  .card--front .brand { left: 28px; top: 58px; gap: 16px; }
  .card--front .brand__square { width: 48px; height: 48px; }
  .card--front .brand__name { font-size: 23px; color: var(--ink); }

  .person { position: absolute; left: 28px; top: 185px; }
  .person__name { font-family: "Jost", sans-serif; font-weight: 600; font-size: 22px; color: var(--brand); letter-spacing: .3px; line-height: 1; }
  .person__role { font-size: 17px; color: var(--ink); margin-top: 3px; }

  .contacts { position: absolute; left: 28px; top: 243px; list-style: none; }
  .contacts li { display: flex; align-items: center; gap: 7px; font-size: 17px; color: var(--ink); height: 21.5px; }
  .contacts svg { width: 15px; height: 15px; flex: none; }
  .contacts .accent { color: var(--brand); }

  .portrait {
    position: absolute; left: 260px; top: 37px; width: 286px; height: 286px; border-radius: 50%;
    background: linear-gradient(180deg, var(--photo-top) 0%, #c9c4c0 45%, var(--photo-bottom) 100%);
  }

  /* Back */
  .card--back {
    left: 263px; top: 623px;
    background: linear-gradient(120deg, var(--brand-light) 0%, var(--brand) 45%, var(--brand-deep) 100%);
    border-radius: 181px 0 0 181px;
  }
  .card--back .brand { left: 144px; top: 133px; gap: 20px; }
  .card--back .brand__square { width: 70px; height: 70px; background: var(--paper); }
  .card--back .brand__name { font-size: 33px; color: var(--paper); letter-spacing: 2px; }
</style>
</head>
<body>

<section class="card card--front" aria-label="Vorderseite">
  <div class="brand">
    <span class="brand__square"></span>
    <p class="brand__name">Lindqvar<br>Staff</p>
  </div>

  <div class="person">
    <h1 class="person__name">MARA HOLTKAMP</h1>
    <p class="person__role">Managing Director</p>
  </div>

  <ul class="contacts">
    <li>
      <svg viewBox="0 0 16 16" aria-hidden="true"><path fill="#ef5f2f" d="M3.2 1.2 5.6 3.6 4.4 5.6c.9 2.2 3.1 4.5 5.9 5.9l2-1.2 2.4 2.4-1.6 2.1C7.3 14.6 1.4 8.7.9 2.8z"/><path fill="none" stroke="#ef5f2f" stroke-width="1.3" d="M9.5 1.5a5 5 0 0 1 5 5M9.3 4a2.6 2.6 0 0 1 2.7 2.6"/></svg>
      <span>030-555 014 227</span>
    </li>
    <li>
      <svg viewBox="0 0 16 16" aria-hidden="true"><rect x="0" y="3" width="16" height="10" fill="#ef5f2f"/><path fill="none" stroke="#fff" stroke-width="1.2" d="M0.5 3.5 8 9l7.5-5.5M.5 12.5l5.5-5M15.5 12.5 10 7.5"/></svg>
      <span>info@lindqvar-staff.de</span>
    </li>
    <li>
      <svg viewBox="0 0 16 16" aria-hidden="true"><g fill="none" stroke="#ef5f2f" stroke-width="1.3"><circle cx="8" cy="8" r="7"/><ellipse cx="8" cy="8" rx="3" ry="7"/><path d="M1 8h14M2 4.5h12M2 11.5h12"/></g></svg>
      <span>www.<span class="accent">lindqvar-staff</span>.de</span>
    </li>
  </ul>

  <div class="portrait" role="img" aria-label="Porträtfoto der Mitarbeiterin im Büro"></div>
</section>

<section class="card card--back" aria-label="Rückseite">
  <div class="brand">
    <span class="brand__square"></span>
    <p class="brand__name">Lindqvar<br>Staff</p>
  </div>
</section>

</body>
</html>
```